Verlindo Magician

I want the business card for my business to give to people who watch that later I will be employed to show magic here is my website http://www.balsamomagicien.com/I want the interesting design , i am very opened for formal and informal, I watch a lot of design so don't stick to the common shape and form but i hope it can also be produced the thing to write on will be the same as in picture that i will upload , i also will upload the logo for you that so can be easy to useDenis CostilleMagicianMAGICIAN BALSAMO 17 rue des Tilleuls - 71400 VAURELAY contact@verlindoillusions.example tel. 0381 946 157 tel. 0674 219 503

```html
<!DOCTYPE html>
<html lang="en">
<head>
<meta charset="utf-8">
<title>Verlindo Magician – Business Card</title>
<link href="https://fonts.googleapis.com/css2?family=Jost:wght@400;500&display=swap" rel="stylesheet">
<style>
  :root {
    --backdrop: #3a3a3a;
    --paper: #ffffff;
    --ink: #1a1a1a;
    --ink-soft: #4a4a4a;
    --accent: #e0232a;
    --band: #111111;
    --divider: #c8c8c8;
  }
  * { margin: 0; padding: 0; box-sizing: border-box; }
  html, body {
    width: 1200px; height: 960px; overflow: hidden;
    background: radial-gradient(ellipse at 50% 45%, #5a5a5a 0%, var(--backdrop) 70%, #262626 100%);
    font-family: "Jost", "Futura", sans-serif;
    color: var(--ink);
  }
  .card {
    position: absolute;
    width: 640px; height: 366px;
    background: var(--paper);
    box-shadow: 0 18px 40px rgba(0,0,0,.45);
    overflow: hidden;
  }
  .card--back { left: 90px; top: 80px; }
  .card--front { left: 470px; top: 510px; }

  .portrait {
    position: absolute;
    background: linear-gradient(180deg, #2a2a2a 0%, #0d0d0d 100%);
    border-radius: 48% 48% 18% 18% / 40% 40% 14% 14%;
  }
  .card--back .portrait { left: 255px; top: 60px; width: 130px; height: 170px; }
  .back-url {
    position: absolute; left: 0; right: 0; top: 286px;
    text-align: center;
    font-size: 13px; letter-spacing: 3px; color: var(--ink-soft);
    white-space: nowrap;
  }

  .card--front .portrait { left: 60px; top: 56px; width: 120px; height: 160px; }
  .brand-name {
    position: absolute; left: 8px; top: 232px; width: 224px;
    text-align: center; white-space: nowrap;
    font-size: 16px; font-weight: 400; letter-spacing: 1px;
    text-transform: uppercase; color: var(--ink);
  }
  .divider {
    position: absolute; left: 238px; top: 40px; width: 1px; height: 230px;
    background: linear-gradient(180deg, transparent, var(--divider) 30%, var(--divider) 70%, transparent);
  }
  .details { position: absolute; left: 270px; top: 48px; right: 20px; }
  .person-name { font-size: 28px; font-weight: 400; line-height: 1.1; }
  .person-role { font-size: 19px; color: var(--accent); margin-bottom: 12px; }
  .company, .address { font-size: 15px; color: var(--ink-soft); letter-spacing: .3px; line-height: 1.35; white-space: nowrap; }
  .contact-list { list-style: none; margin-top: 8px; }
  .contact-list li {
    display: flex; align-items: center; gap: 10px;
    font-size: 15px; color: var(--ink-soft); line-height: 1.45;
    white-space: nowrap;
  }
  .contact-list svg { width: 14px; height: 14px; fill: var(--ink); flex: none; }
  .accent-rule {
    position: absolute; left: 0; right: 0; bottom: 22px; height: 3px;
    background: var(--accent);
  }
  .footer-band {
    position: absolute; left: 0; right: 0; bottom: 0; height: 18px;
    background: var(--band);
  }
</style>
</head>
<body>

<section class="card card--back" aria-label="Card back">
  <div class="portrait" role="img" aria-label="Black and white illustration of the magician holding a playing card"></div>
  <p class="back-url">www.verlindoillusions.example</p>
</section>

<section class="card card--front" aria-label="Card front">
  <div class="portrait" role="img" aria-label="Black and white illustration of the magician holding a playing card"></div>
  <p class="brand-name">Verlindo Magician</p>

  <div class="divider"></div>

  <div class="details">
    <h1 class="person-name">Marc Ravoulet</h1>
    <p class="person-role">Magician</p>
    <p class="company">MAGICIAN VERLINDO</p>
    <p class="address">17 rue des Tilleuls - 71400 VAURELAY</p>
    <ul class="contact-list">
      <li>
        <svg viewBox="0 0 24 24" aria-hidden="true"><path d="M6.6 10.8a15.1 15.1 0 0 0 6.6 6.6l2.2-2.2a1 1 0 0 1 1-.25 11.4 11.4 0 0 0 3.6.57 1 1 0 0 1 1 1V20a1 1 0 0 1-1 1A17 17 0 0 1 3 4a1 1 0 0 1 1-1h3.5a1 1 0 0 1 1 1c0 1.25.2 2.45.57 3.57a1 1 0 0 1-.25 1z"/></svg>
        0381 946 157
      </li>
      <li>
        <svg viewBox="0 0 24 24" aria-hidden="true"><path d="M6.6 10.8a15.1 15.1 0 0 0 6.6 6.6l2.2-2.2a1 1 0 0 1 1-.25 11.4 11.4 0 0 0 3.6.57 1 1 0 0 1 1 1V20a1 1 0 0 1-1 1A17 17 0 0 1 3 4a1 1 0 0 1 1-1h3.5a1 1 0 0 1 1 1c0 1.25.2 2.45.57 3.57a1 1 0 0 1-.25 1z"/></svg>
        0674 219 503
      </li>
      <li>
        <svg viewBox="0 0 24 24" aria-hidden="true"><path d="M2 5h20v14H2z M3.5 6.5v.4l8.5 6 8.5-6v-.4z" fill-rule="evenodd"/></svg>
        contact@verlindoillusions.example
      </li>
      <li>
        <svg viewBox="0 0 24 24" aria-hidden="true"><path d="M12 2a10 10 0 1 0 0 20 10 10 0 0 0 0-20zm-1 17.9A8 8 0 0 1 4.1 11H8c.1 3.3 1.2 6.5 3 8.9zM8 9H4.4A8 8 0 0 1 11 4.1 15 15 0 0 0 8 9zm5 10.9c1.8-2.4 2.9-5.6 3-8.9h3.9a8 8 0 0 1-6.9 8.9zM16 9a15 15 0 0 0-3-4.9A8 8 0 0 1 19.6 9z"/></svg>
        www.verlindoillusions.example
      </li>
    </ul>
  </div>

  <div class="accent-rule"></div>
  <div class="footer-band"></div>
</section>

</body>
</html>
```